Zielgruppe
Ich biete farbtupferei, Glitzertattoos, Schwangerschaftsbemalung (Belly-Painting), Wunden schminken, Vermietung von einer Popcornmaschine.
Aufgabenstellung
Mein Anliegen betrifft hiermit die Gestaltung einer Website.
In Bezug auf die Website gibt es schon eine gekaufte Domain, welche lautet: frau-pinselmaus.de und kann über VERAX eingerichtet werden.
Auf dieser WEBSITE soll sich folgendes Menü befinden:
- Anfrage stellen/Angebot einholen mit zusätzlicher Frage 'Wie sind Sie auf mich aufmerksam geworden?'
Mit einem Feld für den Namen, E-Mail, Telefonnummer, Gewünschtes Datum.
Sowie die Frage 'Wie sind Sie auf mich aufmerksam geworden?' (zum Ankreuzen) Freunde, Empfehlung, Flyer, soziale medienoder sonstiges.
Gerne auch zum ankreuzen welche Leistung Sie möchten. farbtupferei, Glitzer Tattoos, Schwangerschaftsbemalung, oder Popcornmaschiene. (So brauchen haben es die Kunden einfacher nur anzukreuzen und ich sehe gleich worum es sich handelt.)
- eine Leistungsübersicht: farbtupferei, Glitzertattoos, Schwangerschaftsbemalung (Belly-Painting), Wunden schminken, Vermietung von einer Popcornmaschine
- meine Kontaktdaten
- Galerie (es kann eine Auswahl der angehängten Bilder sein)
!!! mein Wunsch wäre, dass sich die Figur von dem Logo in verschiedenen Positionen auf der Website an das Menü angepasst wiederfindet (wenn dies irgendwie machbar ist)
z.B. meine Figur (Logo) stehend am Rand oder liegend.....
- erwünscht ist auch eine Verknüpfung mit einem Findlaeintrag
- Hinweis auf Kontaktor und Lumoravue (bin gerade dabei ein öffentliches Profil dort zu erstellen)
!Wichtig wäre die nötige Einstellung, damit die Website sowohl in der mobilen Version als auch der PC-Version mit ALLEN oben genannten Informationen dargestellt wird!
Dankbar wäre ich noch für die Information, ob für mich laufende Kosten (monatlich oder jährlich) für die Website entstehen?
Mein Logo ist mir sehr wichtig und sollte gut sichtbar und erkennbar sein auch die Schriftart kann auf der Website aufgegriffen werden

```html
<!DOCTYPE html>
<html lang="de">
<head>
<meta charset="utf-8">
<title>Frau Pinselmaus – farbtupferei</title>
<link href="https://fonts.googleapis.com/css2?family=Amatic+SC:wght@400;700&family=Open+Sans:wght@400;600;700&display=swap" rel="stylesheet">
<style>
:root{
  --bg-top:#fbf4d3;
  --bg-bottom:#f8dde3;
  --white:#ffffff;
  --teal:#2a9aa8;
  --teal-dark:#1f7f8c;
  --sky:#dcecf6;
  --peach:#fde3b8;
  --sun:#fdd27a;
  --amber:#f6b53c;
  --pink:#e3507e;
  --ink:#3a3a3a;
  --muted:#777;
  --card:#eef7fb;
}
*{box-sizing:border-box;margin:0;padding:0}
html,body{width:750px;height:1200px;overflow:hidden}
body{background:linear-gradient(180deg,var(--bg-top),var(--bg-bottom));font-family:"Open Sans",sans-serif;color:var(--ink);position:relative}
.page{position:absolute;left:262px;top:45px;width:226px;height:1133px;background:var(--white);display:flex;flex-direction:column;box-shadow:0 1px 4px rgba(0,0,0,.06)}
.hand{font-family:"Amatic SC",cursive;font-weight:700}
.tiny{font-size:3px;line-height:1.35}

/* header */
.hero{height:177px;position:relative}
.nav{display:flex;justify-content:space-between;align-items:center;padding:6px 8px}
.nav .home{width:6px;height:6px;background:var(--teal);clip-path:polygon(50% 0,100% 50%,85% 50%,85% 100%,15% 100%,15% 50%,0 50%)}
.nav ul{list-style:none;display:flex;gap:7px;font-size:3px;color:var(--muted);text-transform:uppercase}
.brand{position:absolute;left:34px;top:32px;width:160px;height:94px}
.brand-name{position:absolute;left:0;top:20px;font-family:"Amatic SC",cursive;font-weight:700;color:var(--teal);font-size:26px;line-height:.95}
.brand-tag{position:absolute;left:0;top:75px;font-size:3.2px;color:var(--teal);text-transform:uppercase;letter-spacing:.2px}
.brand-figure{position:absolute;right:0;top:0;width:62px;height:92px;border-radius:40% 40% 30% 30%;background:linear-gradient(160deg,#f3e3c6,#d8eef2)}
.scroll-dot{position:absolute;left:107px;bottom:10px;width:9px;height:9px;border-radius:50%;background:var(--sun)}

/* about */
.about{height:138px;background:var(--sky);display:flex;align-items:center;gap:10px;padding:0 14px}
.portrait{width:68px;height:68px;border-radius:50%;background:radial-gradient(circle at 50% 40%,#e9c9a8,#b98c64 70%,#eee 72%);flex:none}
.about h2{font-family:"Amatic SC",cursive;font-size:11px;color:var(--ink);margin-bottom:4px}
.about p{color:var(--muted);width:86px}
.btn{display:inline-block;background:var(--sun);color:var(--white);font-size:3px;padding:2px 6px;border-radius:2px;margin-top:6px}

/* offers */
.offers{height:188px;background:var(--teal);position:relative;text-align:center;padding-top:12px}
.section-title{font-family:"Amatic SC",cursive;font-weight:700;font-size:8px;letter-spacing:.4px}
.offers .section-title{color:var(--sun)}
.cards{display:flex;flex-wrap:wrap;justify-content:center;gap:6px 6px;width:190px;margin:12px auto 0}
.card{width:56px;height:52px;background:var(--card);border-radius:3px;padding:3px;display:flex;flex-direction:column;align-items:center}
.card .thumb{width:100%;height:27px;border-radius:2px;background:linear-gradient(135deg,#f2b8c6,#c9dff0)}
.card span{font-size:3px;color:var(--teal-dark);margin-top:4px;line-height:1.3}
.card:nth-child(n+4) .thumb{background:linear-gradient(135deg,#e8b98a,#9bbfcf)}
.wave{position:absolute;left:0;bottom:-1px;width:226px;height:14px}

/* gallery */
.gallery{height:135px;text-align:center;padding-top:12px}
.gallery .section-title{color:var(--pink)}
.slider{display:flex;align-items:center;justify-content:center;gap:3px;margin-top:10px}
.arrow{width:6px;height:8px}
.shot{width:42px;height:52px;background:linear-gradient(135deg,#f1c9b0,#d8b9d8)}
.shot:nth-child(3){background:linear-gradient(135deg,#e9d7a0,#b79a62)}
.shot:nth-child(4){background:linear-gradient(135deg,#f0b8c4,#9ccbe0)}

/* contact */
.contact{height:100px;display:flex}
.contact-info{width:90px;background:var(--peach);padding:14px 10px}
.contact-info .section-title{color:var(--ink);text-align:left;margin-bottom:10px}
.contact-info dt{font-size:3px;font-weight:700;margin-top:5px}
.contact-info dd{font-size:3px;color:var(--muted)}
.contact-photo{flex:1;background:linear-gradient(135deg,#f3a9c0,#f6d37e 45%,#9ed3e6)}

/* form */
.request{height:200px;background:var(--sun);padding:14px 18px 0;text-align:center}
.request .section-title{color:var(--ink);font-size:7px}
.fields{display:grid;grid-template-columns:1fr 1fr;gap:4px 10px;margin-top:10px;text-align:left}
.field{background:var(--white);height:6px;border-radius:1px;font-size:2.8px;color:var(--muted);padding:1px 2px}
.field.tall{height:15px}
.checks{display:grid;grid-template-columns:32px 1fr 32px 1fr;gap:3px 4px;margin-top:8px;text-align:left;font-size:2.8px}
.checks p{grid-row:span 5;color:var(--ink)}
.check{display:flex;align-items:center;gap:2px;background:var(--white);height:5px;padding:0 2px;color:var(--muted)}
.check i{width:2.5px;height:2.5px;border:.4px solid var(--muted)}
.send{display:inline-block;background:var(--amber);color:var(--white);font-size:3px;padding:1.5px 7px;margin-top:12px}

/* reviews */
.reviews{height:142px;text-align:center;padding-top:16px}
.reviews .section-title{color:var(--ink)}
.review-list{display:flex;justify-content:center;gap:14px;margin-top:10px}
.review{width:50px}
.avatar{width:18px;height:18px;margin:0 auto;background:linear-gradient(135deg,#e0c3a5,#c7a184)}
.review h3{font-size:3px;font-weight:700;margin-top:5px;text-transform:uppercase}
.review p{color:var(--muted);margin-top:2px}
.stars{color:var(--pink);font-size:4px;margin-top:2px;letter-spacing:.3px}

/* footer */
.footer{flex:1;background:var(--pink);display:flex;align-items:center;justify-content:space-between;padding:0 14px;position:relative}
.footer .hand{color:var(--white);font-size:7px;font-weight:400}
.social{display:flex;gap:6px}
.social span{display:flex;align-items:center;gap:2px;color:var(--white);font-size:3.5px}
.social i{width:7px;height:7px;border-radius:50%;background:var(--white)}
.legal{position:absolute;bottom:3px;left:0;right:0;text-align:center;font-size:2.5px;color:#f7c3d3}
</style>
</head>
<body>
<main class="page">
  <header class="hero">
    <nav class="nav">
      <span class="home"></span>
      <ul><li>Start</li><li>Angebot</li><li>Galerie</li><li>Kontakt</li></ul>
    </nav>
    <div class="brand">
      <div class="brand-name">Frau<br>Pinselmaus</div>
      <div class="brand-tag">farbtupferei &amp; Glitzertattoos</div>
      <div class="brand-figure" role="img" aria-label="Gezeichnete Logofigur mit Pinsel"></div>
    </div>
    <span class="scroll-dot"></span>
  </header>

  <section class="about">
    <div class="portrait" role="img" aria-label="Porträtfoto der Künstlerin"></div>
    <div>
      <h2>Hallo, schön das du hier bist</h2>
      <p class="tiny">Ich bringe Farbe auf kleine und große Gesichter. Mit viel Liebe zum Detail gestalte ich Motive für Kindergeburtstage, Feste und Feiern. Schau dich gerne um und schick mir deine Anfrage.</p>
      <span class="btn">Mehr erfahren</span>
    </div>
  </section>

  <section class="offers">
    <h2 class="section-title">Mein Angebot</h2>
    <div class="cards">
      <div class="card"><div class="thumb" role="img" aria-label="Foto geschminktes Kind"></div><span>farbtupferei</span></div>
      <div class="card"><div class="thumb" role="img" aria-label="Foto Glitzertattoo"></div><span>Glitzer-Tattoos</span></div>
      <div class="card"><div class="thumb" role="img" aria-label="Foto Bauchbemalung"></div><span>Schwangerschaftsbemalung (Belly-Painting)</span></div>
      <div class="card"><div class="thumb" role="img" aria-label="Foto geschminkte Wunde"></div><span>Wunden schminken</span></div>
      <div class="card"><div class="thumb" role="img" aria-label="Foto Popcornmaschine"></div><span>Vermietung Popcornmaschine</span></div>
    </div>
    <svg class="wave" viewBox="0 0 226 14" preserveAspectRatio="none"><path d="M0 8 C40 -2 80 16 120 8 S190 2 226 8 V14 H0Z" fill="#fff"/></svg>
  </section>

  <section class="gallery">
    <h2 class="section-title">Galerie</h2>
    <div class="slider">
      <svg class="arrow" viewBox="0 0 6 8"><path d="M5 0 L1 4 L5 8" fill="none" stroke="#e3507e" stroke-width="1.4"/></svg>
      <div class="shot" role="img" aria-label="Foto geschminkte Kinder"></div>
      <div class="shot" role="img" aria-label="Foto Popcorn"></div>
      <div class="shot" role="img" aria-label="Foto Glitzerschminke"></div>
      <svg class="arrow" viewBox="0 0 6 8"><path d="M1 0 L5 4 L1 8" fill="none" stroke="#e3507e" stroke-width="1.4"/></svg>
    </div>
  </section>

  <section class="contact">
    <div class="contact-info">
      <h2 class="section-title">Kontakt</h2>
      <dl>
        <dt>Adresse</dt><dd>Malweg 12, 12345 Farbstadt</dd>
        <dt>Telefon</dt><dd>0123 456 7890</dd>
        <dt>E-Mail</dt><dd>hallo@frau-pinselmaus.de</dd>
      </dl>
    </div>
    <div class="contact-photo" role="img" aria-label="Foto fröhliche Kinder mit Konfetti"></div>
  </section>

  <section class="request">
    <h2 class="section-title">Interessiert? Dann schick mir deine Anfrage</h2>
    <div class="fields">
      <div class="field">Name</div><div class="field">Gewünschtes Datum</div>
      <div class="field">E-Mail-Adresse</div><div class="field tall">Nachricht</div>
      <div class="field">Telefon</div>
    </div>
    <div class="checks">
      <p>Wie bist du auf mich aufmerksam geworden?</p>
      <div class="check"><i></i>Freunde</div>
      <p>Welche Leistung möchtest du?</p>
      <div class="check"><i></i>farbtupferei</div>
      <div class="check"><i></i>Empfehlung</div>
      <div class="check"><i></i>Glitzer Tattoos</div>
      <div class="check"><i></i>Flyer</div>
      <div class="check"><i></i>Schwangerschaftsbemalung</div>
      <div class="check"><i></i>Soziale Medien</div>
      <div class="check"><i></i>Popcornmaschine</div>
      <div class="check"><i></i>Sonstiges</div>
      <div class="check"><i></i>Wunden schminken</div>
    </div>
    <span class="send">Senden</span>
  </section>

  <section class="reviews">
    <h2 class="section-title">Was Kunden sagen</h2>
    <div class="review-list">
      <article class="review"><div class="avatar" role="img" aria-label="Kundenfoto"></div><h3>Lena Haller</h3><p class="tiny">Die Kinder waren begeistert, tolle Motive und sehr liebevolle Betreuung auf unserem Fest.</p><div class="stars">★★★★★</div></article>
      <article class="review"><div class="avatar" role="img" aria-label="Kundenfoto"></div><h3>Jonas Kreuz</h3><p class="tiny">Pünktlich, herzlich und kreativ. Wir buchen sie beim nächsten Geburtstag ganz sicher wieder.</p><div class="stars">★★★★★</div></article>
      <article class="review"><div class="avatar" role="img" aria-label="Kundenfoto"></div><h3>Mira Sendt</h3><p class="tiny">Mein Babybauch wurde wunderschön bemalt, die Fotos sind eine bleibende Erinnerung für uns.</p><div class="stars">★★★★★</div></article>
    </div>
  </section>

  <footer class="footer">
    <span class="hand">Folge mir auf Social Media</span>
    <div class="social"><span><i></i>Kontaktor</span><span><i></i>Lumoravue</span></div>
    <div class="legal">Impressum · Datenschutz</div>
  </footer>
</main>
</body>
</html>
```